eBook Cover_H. Lindqvist-Borna
Schnell und zuverlässoig,Änderungswünsche wurden umgehend ausgeführt. Vielen Dank für das tolle Cover zu meinem ersten Buch!
Zielgruppe
freie Roman-Autorin (Erstlingswerk)
Zielgruppe: Lesende (Erwachsene), Frauen
Charakterisierung: magisch-realistischer Familienroman, spielt im Europa der Jetzt-Zeit
Aufgabenstellung
Im ersten Schritt geht es um ein Cover für ein eBook, das aber bei Bedarf als Book on Demand gedruckt werden soll. Es wird daher später Anforderung bzgl. Dicke / Umfang des gedruckten Buches und einer Rückseite geben. Das gewählte Design soll dann dahingehend überarbeitet und finale Druckdaten zur Verfügung gestellt werden. Dies soll von vornherein berücksichtigt werden und im Preis enthalten sein.
Titel: Regen über Glas, Monde im Moos
Autorinnenname: Henrike Lindqvist-Borna
des weiteren auf dem Cover: Roman

```html
<!DOCTYPE html>
<html lang="de">
<head>
<meta charset="utf-8">
<title>Regen über Glas, Monde im Moos – Henrike Lindqvist-Borna</title>
<link rel="stylesheet" href="https://fonts.googleapis.com/css2?family=Cinzel:wght@400;600;700&display=swap">
<style>
  :root {
    --page: #ffffff;
    --sky-top: #0b1328;
    --sky-mid: #2c4a7a;
    --sky-haze: #8a93b4;
    --glow: #f1c79a;
    --ember: #e08a3c;
    --ground: #0c0a0c;
    --type: #ffffff;
  }
  * { margin: 0; padding: 0; box-sizing: border-box; }
  html, body {
    width: 848px;
    height: 1200px;
    overflow: hidden;
    background: var(--page);
  }
  .page {
    position: relative;
    width: 848px;
    height: 1200px;
    background: var(--page);
  }
  .cover {
    position: absolute;
    left: 127px;
    top: 107px;
    width: 605px;
    height: 894px;
    overflow: hidden;
    font-family: "Cinzel", "Times New Roman", serif;
    color: var(--type);
  }
  .cover-art {
    position: absolute;
    inset: 0;
    background:
      radial-gradient(ellipse 70% 30% at 50% 82%, var(--ember) 0%, rgba(224,138,60,0.45) 30%, rgba(224,138,60,0) 70%),
      radial-gradient(ellipse 60% 55% at 50% 55%, rgba(241,199,154,0.55) 0%, rgba(138,147,180,0.35) 45%, rgba(138,147,180,0) 80%),
      linear-gradient(180deg, var(--sky-top) 0%, var(--sky-mid) 38%, var(--sky-haze) 62%, var(--glow) 80%, var(--ground) 86%, var(--ground) 100%);
  }
  .author {
    position: absolute;
    top: 42px;
    left: 0;
    right: 0;
    text-align: center;
    font-weight: 700;
    font-size: 24px;
    letter-spacing: 0.5px;
    text-shadow: 0 1px 3px rgba(0,0,0,0.5);
  }
  .title {
    position: absolute;
    top: 133px;
    left: 0;
    right: 0;
    text-align: center;
    font-weight: 600;
    font-size: 52px;
    line-height: 62px;
    text-shadow: 0 2px 4px rgba(0,0,0,0.5);
  }
  .title .line { display: block; white-space: nowrap; }
  .title .small {
    font-size: 24px;
    text-transform: lowercase;
  }
  .genre {
    position: absolute;
    top: 828px;
    left: 0;
    right: 0;
    text-align: center;
    font-weight: 700;
    font-size: 26px;
    letter-spacing: 1px;
  }
</style>
</head>
<body>
  <main class="page">
    <section class="cover">
      <div class="cover-art" role="img" aria-label="Sternenhimmel mit Milchstraße über einem Berggipfel, auf dem eine Person als Silhouette mit ausgebreiteten Armen im Gegenlicht steht"></div>
      <p class="author">HENRIKE LINDQVIST-BORNA</p>
      <h1 class="title">
        <span class="line">REGEN <span class="small">über</span> GLAS,</span>
        <span class="line">MONDE <span class="small">im</span> MOOS</span>
      </h1>
      <p class="genre">ROMAN</p>
    </section>
  </main>
</body>
</html>
```